Willow Fen Racquet Club (Tennis Country Club)

Racquet and Tennis Country Club in Florida.
This web sight is needed for a Privet Tennis club located in Deerfield Beach city in Florida, USA.
We have 10 clay tennis courts and 2 hard tennis courts, small and cozy swimming pool and a clubhouse (see attached pictures) Attached pictures are for information only because we are under a reconstruction.
Updates

I haven't received any source files and web converted files neither!

Target Market(s)

Adult members, Kids members, Tennis players

Coding

Coded - Design and coding required

Number of Pages Required

3 page

Requirements
Must have
• Logo colors (see attached file)

```html
<!DOCTYPE html>
<html lang="en">
<head>
<meta charset="utf-8">
<title>Willow Fen Racquet Club</title>
<link href="https://fonts.googleapis.com/css2?family=Roboto:wght@400;500;700&display=swap" rel="stylesheet">
<style>
:root{
  --green:#1b5e32;
  --green-dark:#144a26;
  --pale-green:#9cc4a6;
  --ink:#1f1f1f;
  --body:#666;
  --light:#f4f4f4;
  --footer:#1d1d1d;
  --white:#fff;
}
*{box-sizing:border-box;margin:0;padding:0}
html,body{width:1200px;height:3719px;overflow:hidden}
body{position:relative;font-family:"Roboto",Arial,sans-serif;background:var(--white);color:var(--ink)}
.abs{position:absolute}
/* header */
.site-header{left:0;top:0;width:1200px;height:104px;background:var(--white);border-top:6px solid var(--green);z-index:3}
.brand-badge{left:104px;top:6px;width:188px;height:188px;border-radius:50%;background:var(--white);z-index:4;display:flex;flex-direction:column;align-items:center;justify-content:flex-start;padding-top:28px}
.brand-dot{width:56px;height:56px;border-radius:50%;border:4px solid var(--green)}
.brand-name{margin-top:10px;font-size:26px;font-weight:500;color:var(--ink)}
.main-nav{left:392px;top:46px;display:flex;font-size:14px;font-weight:500;z-index:4}
.main-nav a{color:var(--ink);text-decoration:none;margin-right:38px}
.social-top{left:984px;top:36px;display:flex;gap:6px;z-index:4}
.social-top span{width:34px;height:34px;border-radius:50%;background:var(--green)}
/* hero */
.hero{left:0;top:104px;width:1200px;height:548px;background:linear-gradient(100deg,#5d6e4c 0%,#8e8a62 35%,#4f6b4a 60%,#3f6a44 100%)}
.hero-title{left:607px;top:370px;font-size:74px;font-weight:700;color:var(--white)}
.hero-text{left:610px;top:474px;width:500px;font-size:14px;line-height:20px;color:var(--white)}
.btn{display:flex;align-items:center;justify-content:center;font-size:13px;font-weight:700;border-radius:22px}
.hero-btn{left:610px;top:540px;width:124px;height:36px;background:#222;color:var(--white)}
.scroll-down{left:576px;top:626px;width:48px;height:48px;border-radius:50%;background:var(--white);display:flex;align-items:center;justify-content:center;z-index:2}
/* about */
.about{left:0;top:652px;width:1200px;height:654px;background:var(--light)}
.about-photo{left:99px;top:751px;width:508px;height:456px;background:linear-gradient(160deg,#e6e7ea,#9ea3a8 60%,#3f4347)}
.about-box{left:560px;top:798px;width:533px;height:360px;background:var(--green);border:4px solid var(--white);padding:30px 28px;color:var(--white)}
.about-box h2{font-size:42px;font-weight:500;margin-bottom:14px}
.about-box p{font-size:13px;line-height:22px;margin-bottom:6px}
.btn-outline-light{position:absolute;left:24px;bottom:32px;width:128px;height:42px;border:2px solid var(--white);color:var(--white)}
/* features */
.feature-frame{width:342px;height:400px;background:var(--green)}
.feature-photo{width:370px;height:312px;border:4px solid var(--pale-green)}
.feature h3{font-size:40px;font-weight:500;color:var(--ink);margin-bottom:16px}
.feature p{font-size:13px;line-height:22px;color:var(--body);width:510px;margin-bottom:16px}
.feature ul{list-style:none}
.feature li{font-size:13px;color:var(--body);height:30px;display:flex;align-items:center;gap:14px}
.feature li::before{content:"";width:9px;height:9px;border-radius:50%;border:3px solid var(--green)}
.btn-outline{width:128px;height:42px;border:2px solid var(--green);color:var(--ink);margin-top:14px}
/* contact */
.map{left:0;top:2846px;width:1200px;height:476px;background:linear-gradient(135deg,#dfe6ea 0%,#e9e4d6 40%,#9fd0e6 60%,#b9dcec 100%)}
.pin{left:379px;top:3070px}
.address-card{left:293px;top:3161px;width:220px;height:69px;background:var(--white);padding:12px 14px;font-size:13px;line-height:20px;color:#555;box-shadow:0 2px 6px rgba(0,0,0,.15)}
.contact-panel{left:724px;top:2846px;width:374px;height:476px;background:var(--green);color:var(--white);text-align:center}
.contact-panel h2{margin-top:40px;font-size:42px;font-weight:500}
.contact-panel p{margin:8px auto 0;width:280px;font-size:13px;line-height:22px}
.field{left:766px;width:290px;height:40px;background:var(--white);font-size:13px;color:#777;padding:10px 14px}
.submit-btn{left:945px;top:3230px;width:111px;height:38px;background:#1a1a1a;color:var(--white)}
/* footer */
.site-footer{left:0;top:3322px;width:1200px;height:397px;background:var(--footer);color:var(--white)}
.site-footer > *{position:absolute;color:var(--white)}
.foot-dot{left:174px;top:73px;width:86px;height:86px;border-radius:50%;border:5px solid var(--white)}
.foot-name{left:100px;top:168px;width:232px;text-align:center;font-size:36px;font-weight:500}
.foot-head{font-size:17px;font-weight:500}
.foot-item{font-size:13px;line-height:20px;display:flex;gap:14px;align-items:flex-start}
.foot-item svg{flex:none;margin-top:3px}
.subscribe{left:709px;top:156px;width:384px;height:40px;display:flex}
.subscribe .in{flex:1;background:var(--white);border-radius:20px 0 0 20px;font-size:13px;color:#888;padding:11px 18px}
.subscribe .go{width:106px;background:var(--green);color:var(--white);border-radius:0 20px 20px 0;font-size:12px;font-weight:700;display:flex;align-items:center;justify-content:center}
.social-foot{left:710px;top:218px;display:flex;gap:10px}
.social-foot span{width:32px;height:32px;border-radius:50%;background:var(--green)}
.foot-rule{left:0;top:322px;width:1200px;height:1px;background:#333}
.copyright{left:0;top:354px;width:1200px;text-align:center;font-size:13px}
</style>
</head>
<body>

<header class="abs site-header"></header>
<div class="abs brand-badge"><span class="brand-dot"></span><span class="brand-name">Willow Fen</span></div>
<nav class="abs main-nav"><a>HOME</a><a>ABOUT US</a><a>SERVICES</a><a>FEATURES</a><a>NEWS</a><a>CONTACT US</a></nav>
<div class="abs social-top"><span></span><span></span><span></span></div>

<section class="abs hero" role="img" aria-label="Photo of a tennis player serving on a court"></section>
<h1 class="abs hero-title">Willow Fen</h1>
<p class="abs hero-text">Sed ut perspiciatis unde omnis iste natus error sit voluptatem accusantium doloremque laudantium, totam rem aperiam.</p>
<div class="abs btn hero-btn">READ MORE</div>
<div class="abs scroll-down"><svg width="18" height="18" viewBox="0 0 18 18" fill="none" stroke="#333" stroke-width="2"><path d="M4 4l5 5 5-5M4 9l5 5 5-5"/></svg></div>

<section class="abs about"></section>
<div class="abs about-photo" role="img" aria-label="Rendering of the clubhouse building"></div>
<div class="abs about-box">
  <h2>About us</h2>
  <p>Sed ut perspiciatis unde omnis iste natus error sit voluptatem accusantium doloremque laudantium, totam rem aperiam, eaque ipsa quae ab illo inventore veritatis et quasi architecto beatae vitae dicta sunt explicabo.</p>
  <p>Nemo enim ipsam voluptatem quia voluptas sit aspernatur aut odit aut fugit, sed quia consequuntur magni dolores eos qui ratione voluptatem sequi nesciunt porro quisquam est, qui dolorem ipsum quia dolor sit amet.</p>
  <div class="btn btn-outline-light">READ MORE</div>
</div>

<!-- Tennis courts -->
<div class="abs feature-frame" style="left:99px;top:1406px"></div>
<div class="abs feature-photo" style="left:141px;top:1453px;background:linear-gradient(180deg,#5d86c8 0%,#a9c1e0 45%,#3c6d8f 70%,#4b4a46 100%)" role="img" aria-label="Photo of the tennis courts under a blue sky"></div>
<div class="abs feature" style="left:583px;top:1430px">
  <h3>Tennis courts</h3>
  <p>Lorem ipsum dolor sit amet, consectetur adipiscing elit, sed do eiusmod tempor incididunt ut labore et dolore magna aliquenim ad minim veniam, quis nostrud exercitation ullamco laboris nisi ut aliquip ex ea commodo consequat.</p>
  <ul><li>Excepteur sint occaecat cupidatat non proident</li><li>Sunt in culpa qui officia deserunt mollit ani</li><li>Idst laborumarchitecto beatae vitae</li><li>Ut enim ad minim veniamesse cillum dolore..</li></ul>
  <div class="btn btn-outline">READ MORE</div>
</div>

<!-- Swimming pool -->
<div class="abs feature-frame" style="left:682px;top:1877px"></div>
<div class="abs feature-photo" style="left:724px;top:1924px;background:linear-gradient(180deg,#3f5a3a 0%,#6f7f76 25%,#2f7fc4 45%,#1e62a8 100%)" role="img" aria-label="Photo of the swimming pool"></div>
<div class="abs feature" style="left:99px;top:1900px">
  <h3>Swimming pool</h3>
  <p>Lorem ipsum dolor sit amet, consectetur adipiscing elit, sed do eiusmod tempor incididunt ut labore et dolore magna aliquenim ad minim veniam, quis nostrud exercitation ullamco laboris nisi ut aliquip ex ea commodo consequat.</p>
  <ul><li>Excepteur sint occaecat cupidatat non proident</li><li>Sunt in culpa qui officia deserunt mollit ani</li><li>Idst laborumarchitecto beatae vitae</li><li>Ut enim ad minim veniamesse cillum dolore..</li></ul>
  <div class="btn btn-outline">READ MORE</div>
</div>

<!-- Clubhouse -->
<div class="abs feature-frame" style="left:99px;top:2348px"></div>
<div class="abs feature-photo" style="left:141px;top:2395px;background:linear-gradient(160deg,#d9d9d9 0%,#8a8a8a 50%,#5a5f56 100%)" role="img" aria-label="Rendering of the clubhouse from above"></div>
<div class="abs feature" style="left:583px;top:2372px">
  <h3>Clubhouse</h3>
  <p>Lorem ipsum dolor sit amet, consectetur adipiscing elit, sed do eiusmod tempor incididunt ut labore et dolore magna aliquenim ad minim veniam, quis nostrud exercitation ullamco laboris nisi ut aliquip ex ea commodo consequat.</p>
  <ul><li>Excepteur sint occaecat cupidatat non proident</li><li>Sunt in culpa qui officia deserunt mollit ani</li><li>Idst laborumarchitecto beatae vitae</li><li>Ut enim ad minim veniamesse cillum dolore..</li></ul>
  <div class="btn btn-outline">READ MORE</div>
</div>

<!-- Contact -->
<section class="abs map" role="img" aria-label="Street map of the club's beachside neighbourhood"></section>
<svg class="abs pin" width="40" height="54" viewBox="0 0 40 54"><path d="M20 2C10 2 2 10 2 20c0 13 18 32 18 32s18-19 18-32C38 10 30 2 20 2z" fill="#d93025"/><circle cx="20" cy="20" r="6" fill="#fff"/></svg>
<div class="abs address-card">23,Excepteur sint occaecatcupi Beach city in Florida, USA.</div>
<div class="abs contact-panel">
  <h2>Contact us</h2>
  <p>Excepteur sint occaecat cupidatat non proident sunt in culpa qui ofmmodo coficia</p>
</div>
<div class="abs field" style="top:3014px">Name</div>
<div class="abs field" style="top:3064px">Email</div>
<div class="abs field" style="top:3114px;height:99px">Subject</div>
<div class="abs btn submit-btn">SUBMIT</div>

<!-- Footer -->
<footer class="abs site-footer">
  <span class="foot-dot"></span>
  <div class="foot-name">Willow Fen</div>
  <div class="foot-head" style="left:409px;top:72px">CONTACT US</div>
  <div class="foot-item" style="left:409px;top:112px;width:240px">
    <svg width="14" height="14" viewBox="0 0 14 14" fill="#fff"><path d="M7 1L1 6.5h2V13h3V9h2v4h3V6.5h2z"/></svg>
    <span>23,Excepteur sint occaecatcupi Beach city in Florida, USA.</span></div>
  <div class="foot-item" style="left:409px;top:172px">
    <svg width="14" height="14" viewBox="0 0 14 14" fill="#fff"><path d="M3 1l2.5 3-1.5 1.5c1 2 2.5 3.5 4.5 4.5L10 8.5l3 2.5-1.5 2C6.5 13 1 7.5 1 2.5z"/></svg>
    <span>Phone : 1 555 010 2040</span></div>
  <div class="foot-item" style="left:409px;top:209px">
    <svg width="14" height="14" viewBox="0 0 14 14" fill="#fff"><path d="M1 3h12v8H1z"/><path d="M1 3l6 5 6-5" stroke="#1d1d1d" fill="none"/></svg>
    <span>Email : info@willowfenclub.com</span></div>
  <div class="foot-head" style="left:709px;top:72px">STAY CONNECTED</div>
  <div class="foot-item" style="left:709px;top:112px">Excepteur sint occaecat cupidatat non proidentsunt</div>
  <div class="subscribe"><span class="in">Enter Email</span><span class="go">SUBSCRIBE</span></div>
  <div class="social-foot"><span></span><span></span><span></span><span></span><span></span><span></span><span></span><span></span></div>
  <div class="foot-rule"></div>
  <div class="copyright">Copyright © 2018 Willow Fen.All Rights Reserved &nbsp;|&nbsp; Terms of Service &nbsp;|&nbsp; Privacy Policy</div>
</footer>

</body>
</html>
```